Brightway Carpet and Tile cleaning Business card Design

I need a design that has the same feel as my van.
i would also like a prominent "Review us on facebook" somewhere, but not that it makes it look silly.
I would like the card to have a little bit of grey or black in the design as well.

It will need contact details
phone: 0455 817264
email: rkbrightwayclean@mailbox-example.com
website: www.brightwaycarpetandtilecleaning-example.com.au
facebook: /brightwaycarpetandtilecleaning

Industry/Entity Type

Business

Contact Information for Business Card

Phone number 0455817264
Email rkbrightwayclean@mailbox-example.com
Website www.brightwaycarpetandtilecleaning-example.com.au
Facebook/brightwaycarpetandtilecleaning

Colors
000000

Requirements
Must have
• Same feel as my van
• I want the card to stand out from the crowd
Nice to have
• Maybe include a tiny bit of a third colour? Grey's,blacks, orange?

```html
<!DOCTYPE html>
<html lang="en">
<head>
<meta charset="utf-8">
<title>Brightway Carpet and Tile Cleaning – Business Card</title>
<link rel="stylesheet" href="https://fonts.googleapis.com/css2?family=Open+Sans:wght@400;600&family=Saira:wght@500;600;700&display=swap">
<style>
  :root {
    --backdrop: #3a3a3a;
    --card-white: #ffffff;
    --brand-blue: #1aa3d8;
    --brand-green: #7cc242;
    --ink-grey: #5d5d5d;
    --rule-grey: #c9c9c9;
    --sky-light: #29b9e6;
    --sky-deep: #0f9fd3;
    --white: #ffffff;
  }
  * { box-sizing: border-box; margin: 0; padding: 0; }
  html, body {
    width: 1105px;
    height: 1200px;
    overflow: hidden;
    background: var(--backdrop);
  }
  .canvas {
    position: relative;
    width: 1105px;
    height: 1200px;
  }
  .card {
    position: absolute;
    left: 196px;
    width: 720px;
    height: 412px;
    overflow: hidden;
  }
  .card--front { top: 146px; background: var(--card-white); }
  .card--back  { top: 602px; background: var(--sky-deep); }

  .wordmark {
    position: absolute;
    left: 0;
    width: 100%;
    text-align: center;
    font-family: "Saira", sans-serif;
    font-weight: 700;
    line-height: 1;
  }
  .wordmark__name { display: block; font-size: 78px; letter-spacing: -1px; }
  .wordmark__tagline { display: block; font-size: 22px; letter-spacing: 3px; margin-top: 4px; text-transform: uppercase; }
  .card--front .wordmark { top: 112px; color: var(--brand-blue); }
  .card--back .wordmark { top: 144px; color: var(--white); }

  .holder {
    position: absolute;
    right: 432px;
    top: 276px;
    text-align: right;
    font-family: "Saira", sans-serif;
    font-weight: 600;
    line-height: 1;
  }
  .holder__name { font-size: 25px; color: var(--brand-blue); letter-spacing: 0.5px; }
  .holder__role { font-size: 19px; color: var(--brand-green); margin-top: 10px; font-weight: 500; }

  .divider {
    position: absolute;
    left: 313px;
    top: 262px;
    width: 1px;
    height: 86px;
    background: var(--rule-grey);
  }

  .contacts {
    position: absolute;
    left: 344px;
    top: 264px;
    list-style: none;
    font-family: "Open Sans", sans-serif;
    font-size: 17px;
    color: var(--ink-grey);
  }
  .contacts li {
    display: flex;
    align-items: center;
    height: 27.5px;
  }
  .contacts svg { width: 16px; height: 16px; margin-right: 12px; flex: none; fill: var(--brand-blue); }

  .bubble-field {
    position: absolute;
    inset: 0;
    background:
      linear-gradient(112deg, transparent 52%, rgba(255,255,255,0.18) 57%, rgba(255,255,255,0.08) 66%, transparent 74%),
      radial-gradient(circle at 30% 40%, var(--sky-light), var(--sky-deep) 80%);
  }

  .back-lines {
    position: absolute;
    left: 0;
    width: 100%;
    text-align: center;
    font-family: "Saira", sans-serif;
    font-weight: 600;
    color: var(--white);
    line-height: 1;
  }
  .back-lines__web { top: 323px; font-size: 20px; letter-spacing: 0.5px; }
  .back-lines__review { top: 356px; font-size: 19px; display: flex; justify-content: center; align-items: center; gap: 8px; }
  .review-square { width: 15px; height: 15px; background: var(--white); }
</style>
</head>
<body>
<main class="canvas">

  <section class="card card--front" aria-label="Business card front">
    <div class="wordmark">
      <span class="wordmark__name">Brightway</span>
      <span class="wordmark__tagline">Carpet &amp; Tile Cleaning</span>
    </div>

    <div class="holder">
      <p class="holder__name">DANIEL REEVE</p>
      <p class="holder__role">CEO/FOUNDER</p>
    </div>

    <div class="divider"></div>

    <ul class="contacts">
      <li>
        <svg viewBox="0 0 24 24" aria-hidden="true"><path d="M6.6 10.8a15.1 15.1 0 0 0 6.6 6.6l2.2-2.2a1 1 0 0 1 1-.25 11.4 11.4 0 0 0 3.6.57 1 1 0 0 1 1 1V20a1 1 0 0 1-1 1A17 17 0 0 1 3 4a1 1 0 0 1 1-1h3.5a1 1 0 0 1 1 1c0 1.25.2 2.45.57 3.6a1 1 0 0 1-.25 1z"/></svg>
        0455817264
      </li>
      <li>
        <svg viewBox="0 0 24 24" aria-hidden="true"><path d="M2 5h20v14H2z M3.5 6.5 12 13l8.5-6.5" fill="none" stroke="var(--brand-blue)" stroke-width="2"/></svg>
        rkbrightwayclean@mailbox-example.com
      </li>
      <li>
        <svg viewBox="0 0 24 24" aria-hidden="true"><rect x="3" y="3" width="18" height="18"/></svg>
        brightwaycarpetandtilecleaning
      </li>
    </ul>
  </section>

  <section class="card card--back" aria-label="Business card back">
    <div class="bubble-field" role="img" aria-label="Soft bubble pattern with a light diagonal sheen"></div>

    <div class="wordmark">
      <span class="wordmark__name">Brightway</span>
      <span class="wordmark__tagline">Carpet &amp; Tile Cleaning</span>
    </div>

    <p class="back-lines back-lines__web">WWW.BRIGHTWAYCARPETANDTILECLEANING-EXAMPLE.COM</p>
    <p class="back-lines back-lines__review">REVIEW US ON <span class="review-square"></span></p>
  </section>

</main>
</body>
</html>
```